Tidal Brew Label design/Graphic design

The Company
Tidal brew is an exciting new brand of ‘fit beer’ targeted at fitness enthusiasts as well as beer lovers. Tidal brew is a craft beer with added protein which can be used as a post work out recovery/leisure beverage. The target audience is generally male, 18-30 years old.
We need label/graphic design of the product to appear on our website www.tidalbrewco.co.uk

The Project
The project is to submit four designs, one for each flavour:
• Larger
• Honey Ale
• Banana Ale
• Zero Alcohol

The design of each flavour must be differentiated, yet have a consistent theme throughout all flavours. At this point Tidal brew has no official logo so feel free to incorporate this into the design, although this is not absolutely necessary.

The label/design should include the following basic information:
Brand name: Tidal Brew
Type: Larger/Honey Ale/Banana Ale/Zero
Tag: 7g High Quality Protein
Alcohol percentage: 4%/Vol (0%/Vol for the Zero alcohol version)
Volume: 300ml

Brand Guidelines (designs not necessarily limited to these)
Font: Aldrich
Main Colours: Blue # 005fbf Orange # ed7000
Basic beer bottle image attached.

The final design will be displayed on (but not limited to) the website www.tidalbrewco.co.uk

The winning designer may be contacted for future projects and opportunities with Tidal Brew.

Reason: My apologies I have been sick the last few days and have been unable to provide feedback. Your work is much appreciated, I will extend the project to give us a little more time and provide feedback individually later today. Best Regards, Oliver

Target Market(s)

The target audience is generally male, 18-30 years old.

Industry/Entity Type

Fitness

Requirements
Must have
• The label/design should include the following basic information:
Brand name: Tidal Brew
Volume: 300ml

```html
<!DOCTYPE html>
<html lang="en">
<head>
<meta charset="utf-8">
<title>Tidal Brew – Banana Ale Label</title>
<link rel="stylesheet" href="https://fonts.googleapis.com/css2?family=Cinzel:wght@600&family=Oswald:wght@400;500;600&display=swap">
<style>
  :root {
    --label-yellow: #f1b51b;
    --badge-black: #1e1a17;
    --badge-cream: #f4d27c;
    --burst-light: #f7dc95;
    --burst-deep: #eab548;
    --rule-white: #ffffff;
    --page-bg: #ffffff;
    --wheat-tone: #e7c063;
  }
  html, body {
    margin: 0;
    padding: 0;
    width: 1200px;
    height: 848px;
    overflow: hidden;
    background: var(--page-bg);
  }
  .label {
    display: block;
    width: 1200px;
    height: 848px;
  }
  .label__panel { fill: var(--label-yellow); }
  .badge__body { fill: var(--badge-black); }
  .badge__ring { fill: none; stroke: var(--rule-white); stroke-width: 3; }
  .badge__band { fill: var(--badge-black); }
  .badge__rule { fill: none; stroke: var(--rule-white); stroke-width: 4; }
  .badge__burst-edge { fill: none; stroke: var(--rule-white); stroke-width: 3; }
  .badge__flavour {
    font-family: "Cinzel", Georgia, serif;
    font-weight: 600;
    font-size: 34px;
    letter-spacing: 7px;
    fill: var(--badge-cream);
  }
  .badge__brand {
    font-family: "Oswald", "Arial Narrow", sans-serif;
    font-weight: 500;
    fill: var(--badge-cream);
  }
  .badge__brand--top { font-size: 130px; }
  .badge__brand--bottom { font-size: 262px; }
  .badge__star { fill: var(--rule-white); }
  .badge__seal { fill: var(--badge-black); stroke: var(--rule-white); stroke-width: 4; }
  .badge__ornament { fill: var(--badge-black); opacity: 0.85; }
  .badge__wheat { fill: var(--wheat-tone); }
  .info {
    font-family: "Oswald", "Arial Narrow", sans-serif;
    fill: var(--badge-black);
  }
  .info--tag { font-size: 26px; font-weight: 500; letter-spacing: 1px; }
  .info--small { font-size: 22px; font-weight: 500; }
  .info--big { font-size: 74px; font-weight: 500; }
  .info--volume { font-size: 56px; font-weight: 600; }
</style>
</head>
<body>
<svg class="label" viewBox="0 0 1200 848" xmlns="http://www.w3.org/2000/svg">
  <defs>
    <radialGradient id="burst-fill" cx="50%" cy="50%" r="60%">
      <stop offset="0%" stop-color="var(--burst-light)"/>
      <stop offset="100%" stop-color="var(--burst-deep)"/>
    </radialGradient>
    <clipPath id="badge-inner">
      <ellipse cx="600" cy="424" rx="292" ry="378"/>
    </clipPath>
    <path id="flavour-arc" d="M 380 232 A 240 175 0 0 1 820 232"/>
  </defs>

  <!-- label panel -->
  <rect class="label__panel" x="198" y="79" width="804" height="690"/>

  <!-- side information -->
  <text class="info info--tag" transform="translate(206 96) rotate(90)">7G HIGH QUALITY PROTEIN</text>
  <text class="info info--small" x="204" y="672">ALC.</text>
  <text class="info info--big" x="244" y="700">4%</text>
  <text class="info info--small" x="204" y="760" style="font-size:27px">BY VOLUME</text>
  <text class="info info--small" x="994" y="697" text-anchor="end">VOL.</text>
  <text class="info info--volume" x="996" y="762" text-anchor="end">300ML</text>

  <!-- badge -->
  <g class="badge">
    <ellipse class="badge__body" cx="600" cy="424" rx="308" ry="394"/>
    <ellipse class="badge__ring" cx="600" cy="424" rx="292" ry="378"/>

    <g clip-path="url(#badge-inner)">
      <ellipse cx="600" cy="466" rx="200" ry="268" fill="url(#burst-fill)" role="img" aria-label="Golden sunburst rays behind the badge"/>
      <ellipse class="badge__burst-edge" cx="600" cy="466" rx="200" ry="268"/>
      <path class="badge__band" d="M 280 306 Q 600 284 920 306 L 920 628 Q 600 650 280 628 Z"/>
      <path class="badge__rule" d="M 280 300 Q 600 278 920 300"/>
      <path class="badge__rule" d="M 280 634 Q 600 656 920 634"/>
    </g>

    <text class="badge__flavour">
      <textPath href="#flavour-arc" startOffset="50%" text-anchor="middle">BANANA ALE</textPath>
    </text>

    <rect class="badge__ornament" x="500" y="212" width="200" height="78" rx="6" role="img" aria-label="Barbell emblem with a small scroll ornament"/>

    <polygon class="badge__star" points="339,331 345,347 362,347 348,357 353,374 339,364 325,374 330,357 316,347 333,347"/>
    <polygon class="badge__star" points="861,331 867,347 884,347 870,357 875,374 861,364 847,374 852,357 838,347 855,347"/>

    <text class="badge__brand badge__brand--top" x="600" y="421" text-anchor="middle" textLength="430" lengthAdjust="spacing">TIDAL</text>
    <text class="badge__brand badge__brand--bottom" x="600" y="628" text-anchor="middle" textLength="420" lengthAdjust="spacingAndGlyphs">BREW</text>

    <rect class="badge__wheat" x="432" y="680" width="108" height="56" rx="20" role="img" aria-label="Wheat sprig, left"/>
    <rect class="badge__wheat" x="660" y="680" width="108" height="56" rx="20" role="img" aria-label="Wheat sprig, right"/>

    <circle class="badge__seal" cx="600" cy="713" r="45"/>
    <polygon class="badge__star" points="600,684 607,703 628,703 611,715 617,735 600,723 583,735 589,715 572,703 593,703"/>
  </g>
</svg>
</body>
</html>
```